business card deign

Logo needs the following on it.
1. attached logo
2. Tagline - "If it keeps a drink cold or the party going...we do it!"
3. Name- Dalton Pikes, Founder and CPO
4. Address - 412 E. Carver Avenue, Ste 2207, Tampa, FL. 33917
5. Phone - 555.318.4726

```html
<!DOCTYPE html>
<html lang="en">
<head>
<meta charset="utf-8">
<title>Kelvo Business Card</title>
<link href="https://fonts.googleapis.com/css2?family=Roboto:wght@400;500;700;900&display=swap" rel="stylesheet">
<style>
  :root {
    --backdrop: #232323;
    --card-black: #1b1b1b;
    --ink-white: #ffffff;
    --ink-soft: #e6e6e6;
    --pattern-light: #6a6a6a;
    --pattern-mid: #2c2c2c;
    --pattern-dark: #141414;
  }
  * { box-sizing: border-box; margin: 0; padding: 0; }
  html, body {
    width: 1200px; height: 780px; overflow: hidden;
    background: var(--backdrop);
    font-family: "Roboto", Arial, sans-serif;
  }
  .sheet {
    width: 1200px; height: 780px;
    display: flex; align-items: center; justify-content: center; gap: 40px;
  }
  .card {
    position: relative;
    width: 560px; height: 320px;
    border-radius: 24px;
    overflow: hidden;
    background: var(--card-black);
    box-shadow: 0 14px 30px rgba(0,0,0,.45);
  }
  /* Back side */
  .card-back .pattern-field {
    position: absolute; inset: 0;
    background: linear-gradient(125deg, var(--pattern-light) 0%, var(--pattern-mid) 35%, var(--pattern-dark) 75%);
  }
  /* Front side */
  .front-art { position: absolute; inset: 0; }
  .brand-name {
    position: absolute;
    left: 330px; top: 138px;
    width: 220px; text-align: center;
    font-size: 40px; font-weight: 700; letter-spacing: 10px;
    color: var(--card-black);
  }
  .identity {
    position: absolute; left: 28px; top: 52px;
    padding-left: 18px;
    color: var(--ink-white);
  }
  .identity::before {
    content: ""; position: absolute; left: 0; top: 10px;
    width: 10px; height: 46px; background: var(--ink-white);
  }
  .person-name { font-size: 29px; font-weight: 900; line-height: 1.1; }
  .person-role { font-size: 15px; font-weight: 400; margin-top: 3px; color: var(--ink-soft); }
  .tagline {
    position: absolute; left: 40px; top: 196px;
    font-size: 12.5px; line-height: 1.45; color: var(--ink-white);
  }
  .contact-list {
    position: absolute; left: 40px; top: 244px;
    list-style: none; color: var(--ink-white);
    font-size: 12.5px; line-height: 1.45;
  }
  .contact-list li { display: flex; gap: 8px; align-items: flex-start; }
  .contact-list svg { width: 13px; height: 13px; margin-top: 2px; flex: none; }
</style>
</head>
<body>
<main class="sheet">

  <section class="card card-back" aria-label="Card back">
    <div class="pattern-field" role="img" aria-label="Repeating brand symbol pattern in glossy black with a silver sheen fading from the top left"></div>
  </section>

  <section class="card card-front" aria-label="Card front">
    <svg class="front-art" viewBox="0 0 560 320" aria-hidden="true">
      <circle cx="440" cy="140" r="206" fill="var(--ink-white)"/>
      <circle cx="452" cy="132" r="200" fill="var(--card-black)"/>
      <circle cx="456" cy="128" r="196" fill="var(--ink-white)"/>
    </svg>
    <div class="brand-name">KELVO</div>

    <div class="identity">
      <h1 class="person-name">Dalton Pikes</h1>
      <p class="person-role">Founder and CPO</p>
    </div>

    <p class="tagline">If it keeps a drink cold or<br>the party going...we do it!</p>

    <ul class="contact-list">
      <li>
        <svg viewBox="0 0 24 24" fill="none" stroke="currentColor" stroke-width="2.4" stroke-linecap="round"><path d="M5 3h4l2 5-3 2a11 11 0 0 0 6 6l2-3 5 2v4a2 2 0 0 1-2 2A17 17 0 0 1 3 5a2 2 0 0 1 2-2z"/></svg>
        <span>555.318.4726</span>
      </li>
      <li>
        <svg viewBox="0 0 24 24" fill="none" stroke="currentColor" stroke-width="2.4"><path d="M12 22s7-7 7-12a7 7 0 0 0-14 0c0 5 7 12 7 12z"/><circle cx="12" cy="10" r="2.5"/></svg>
        <span>412 E. Carver Avenue,<br>Ste 2207, Tampa, FL. 33917</span>
      </li>
    </ul>
  </section>

</main>
</body>
</html>
```